Business Card Design Project

Looking to update our business cards. We have a logo with our slogan. We are an IT firm so we wouldlike a modern look.

Industry/Entity Type

Business

```html
<!DOCTYPE html>
<html lang="en">
<head>
<meta charset="utf-8">
<title>Business Card Variants</title>
<link rel="stylesheet" href="https://fonts.googleapis.com/css2?family=Josefin+Sans:wght@400;600&display=swap">
<style>
  :root {
    --page-bg: #e8e5e1;
    --band-black: #000000;
    --brand-green: #6f8f3c;
    --slogan-white: #ffffff;
    --silver-light: #dcdcdc;
    --silver-dark: #9c9c9c;
    --red-light: #b73c2f;
    --red-dark: #550e0e;
  }
  * { margin: 0; padding: 0; box-sizing: border-box; }
  html, body {
    width: 1200px;
    height: 1181px;
    overflow: hidden;
    background: var(--page-bg);
  }
  .canvas {
    position: relative;
    width: 1200px;
    height: 1181px;
  }
  .card {
    position: absolute;
    left: 192px;
    width: 816px;
    height: 469px;
    overflow: hidden;
  }
  .card--silver {
    top: 84px;
    background: radial-gradient(ellipse 60% 70% at 50% 50%, var(--silver-light), var(--silver-dark));
  }
  .card--red {
    top: 617px;
    background: radial-gradient(ellipse 55% 65% at 50% 50%, var(--red-light), var(--red-dark));
  }
  .brand-band {
    position: absolute;
    left: 0;
    top: 177px;
    width: 100%;
    height: 116px;
    background: var(--band-black);
  }
  .brand-lockup {
    position: absolute;
    left: 0;
    top: 0;
    width: 100%;
    height: 100%;
    display: flex;
    flex-direction: column;
    align-items: center;
    justify-content: center;
    gap: 12px;
    padding-top: 8px;
  }
  .brand-name {
    font-family: "Josefin Sans", sans-serif;
    font-weight: 600;
    font-size: 54px;
    line-height: 1;
    letter-spacing: 11px;
    color: var(--brand-green);
    padding-left: 11px;
  }
  .brand-slogan {
    font-family: "Josefin Sans", sans-serif;
    font-weight: 600;
    font-size: 18px;
    line-height: 1;
    letter-spacing: 5px;
    color: var(--slogan-white);
    padding-left: 5px;
  }
</style>
</head>
<body>
<main class="canvas">
  <section class="card card--silver">
    <div class="brand-band">
      <div class="brand-lockup">
        <span class="brand-name">KERNELWAY</span>
        <span class="brand-slogan">MAKING TECHNOLOGY EASIER</span>
      </div>
    </div>
  </section>

  <section class="card card--red">
    <div class="brand-band">
      <div class="brand-lockup">
        <span class="brand-name">KERNELWAY</span>
        <span class="brand-slogan">MAKING TECHNOLOGY EASIER</span>
      </div>
    </div>
  </section>
</main>
</body>
</html>
```